skyPARLOR Helicopter Tour WordPress Website Design

SkyPARLOR (skyparlor-example.com) is a premium helicopter tour company offering scenic flights in two Florida cities: Tampa and Sarasota. We are seeking a full Wordpress website redesign that is modern, upbeat, inviting, and highly conversion‑focused. The new site should feel energetic and trustworthy, reflect the excitement of helicopter sightseeing, and maintain our recognizable SkyPARLOR color palette—while updating the overall look to feel fresh, clean, and current.
The website must be SEO‑friendly, mobile‑optimized, and easy to navigate. It should highlight our 5‑star customer reviews, showcase our tours clearly, and integrate seamlessly with TrailDock for instant online booking. The design should support a premium aviation experience while remaining friendly and accessible to tourists, families, couples, and adventure seekers.

These elements are essential and must be included in the design:

Brand & UX:
- Modern, upbeat, inviting design
- SEO‑friendly structure and layout
- Easy navigation and clear user flow
- Light grey “SP” background logo watermark (as used on current site)
- Clean, aviation‑inspired typography and layout

Conversion Features:
- Instant booking above the fold (TrailDock integration)
- Live Orbin Ratings carousel
- Tour comparison table (duration, route, price, etc.)
- FAQ expandable section
- Gift Cards page (highlighted as a major offering)
- What to Expect timeline (Arrive → Check‑In → Safety Briefing → Flight → Photos)
- Weather transparency widget (clear messaging about weather‑dependent flights

Content Structure:
- Separate pages for Tampa, Sarasota, and Gender Reveal Flights
- Pilot/Team profiles with short bios
- Highlighted features:
- Doors‑Off option
- Sunset flights
- Romantic packages
- Champagne add‑ons

Colors:
Use the existing SkyPARLOR palette as the foundation, but modernize it.
- Background: Clean with the light grey “SP” watermark integrated tastefully.
The overall color direction should feel bright, premium, energetic, and trustworthy

Target Market(s)

Tourists visiting Tampa or Sarasota, Families looking for memorable activities, Couples seeking romantic experiences (sunset flights, proposals, anniversaries), Adventure seekers and content creators, Locals celebrating birthdays, holidays, or special occasions, Gender reveal clients looking for a unique aerial reveal experience

Industry/Entity Type

Travel & Tourism / Aviation / Helicopter Tours / Experience‑based Activities

Requirements
Must have
• These elements are essential and must be included in the design: Brand & UX - Modern, upbeat, inviting design / SEO‑friendly structure and layout / Easy navigation and clear user flow / Light grey “SP” background logo watermark (as used on current site) / Clean, aviation‑inspired typography and layout
Nice to have
• Interactive route map showing flight paths / Subtle motion or parallax effects in hero sections / Animated icons or micro‑interactions / Social media integration (Instagram grid, TikTok clips) / Sticky mobile booking bar / Video header or short aerial footage loop / Subtle aviation‑themed graphic elements (rotor blur, sky gradients, etc.
Should not have
• No dark, heavy, or overly moody themes / No outdated fonts or overly playful typography / No cluttered layouts or excessive text blocks / No stocky, generic tourism imagery / No slow‑loading animations or heavy effects that hurt SEO

```html
<!DOCTYPE html>
<html lang="en">
<head>
<meta charset="UTF-8">
<title>SkyPARLOR Helicopter Tours</title>
<link href="https://fonts.googleapis.com/css2?family=Oswald:wght@500;600;700&family=Poppins:wght@400;500;600;700&display=swap" rel="stylesheet">
<style>
:root{
  --blue:#1f5fa8;
  --blue-dark:#174a86;
  --ink:#141414;
  --text:#444;
  --muted:#777;
  --line:#e4e4e4;
  --soft:#f2f3f5;
  --white:#fff;
  --footer:#121212;
}
*{box-sizing:border-box;margin:0;padding:0}
html,body{width:1200px;height:4376px;overflow:hidden}
body{font-family:"Poppins",sans-serif;color:var(--text);background:var(--white);position:relative}
h1,h2,h3{font-family:"Oswald",sans-serif;color:var(--ink);text-transform:uppercase;font-weight:600}
.btn{display:inline-block;background:var(--blue);color:var(--white);font-size:13px;font-weight:600;padding:12px 24px;border-radius:4px;text-decoration:none}
.section-title{text-align:center;font-size:38px;letter-spacing:.5px}

/* hero */
.hero{position:relative;height:700px;overflow:hidden}
.hero-photo{position:absolute;inset:0;background:linear-gradient(115deg,#2a2d33 0%,#4a5058 40%,#8d949b 70%,#5c636b 100%)}
.hero-shade{position:absolute;inset:0;background:linear-gradient(90deg,rgba(0,0,0,.55) 0%,rgba(0,0,0,.15) 55%,rgba(0,0,0,0) 100%)}
.nav{position:absolute;top:0;left:0;right:0;height:96px;display:flex;align-items:center;justify-content:space-between;padding:0 72px;z-index:2}
.brand{display:flex;align-items:center;gap:10px;color:var(--white);font-weight:700;font-size:20px;text-decoration:none}
.brand-dot{width:34px;height:34px;border-radius:50%;background:var(--blue)}
.menu{display:flex;align-items:center;gap:30px;list-style:none}
.menu a{color:var(--white);font-size:13px;text-decoration:none}
.hero-copy{position:absolute;left:72px;top:176px;z-index:2}
.hero-copy h1{color:var(--white);font-size:86px;line-height:.98;font-weight:700}
.hero-copy p{color:var(--white);font-family:"Oswald",sans-serif;font-size:22px;letter-spacing:1px;text-transform:uppercase;margin:20px 0 34px}

/* booking */
.booking{position:absolute;left:140px;top:642px;width:920px;height:118px;background:var(--white);border-radius:16px;box-shadow:0 10px 30px rgba(0,0,0,.12);display:flex;align-items:center;gap:16px;padding:0 28px;z-index:3}
.field{flex:1}
.field label{display:block;font-size:12px;font-weight:600;color:var(--ink);margin-bottom:8px}
.field span{display:block;background:var(--soft);border-radius:6px;font-size:13px;color:var(--muted);padding:11px 14px}
.search{width:44px;height:44px;border-radius:6px;background:var(--blue);margin-top:22px;display:flex;align-items:center;justify-content:center}

/* reviews */
.reviews{position:absolute;top:820px;left:0;width:1200px}
.rating-name{text-align:center;font-weight:600;font-size:22px;color:var(--ink);margin-top:12px}
.review-row{display:flex;gap:22px;justify-content:center;margin-top:38px}
.review{width:334px;height:200px;border:1px solid var(--line);border-radius:10px;padding:22px;background:var(--white)}
.review-head{display:flex;align-items:center;gap:10px;margin-bottom:14px}
.avatar{width:38px;height:38px;border-radius:50%;color:var(--white);font-weight:600;display:flex;align-items:center;justify-content:center}
.review-head b{display:block;font-size:13px;color:var(--ink)}
.stars{color:#f5b301;font-size:12px;letter-spacing:1px}
.review p{font-size:12px;line-height:1.6}
.review a{display:inline-block;margin-top:8px;font-size:12px;font-weight:600;color:var(--blue);text-decoration:none}
.dots{display:flex;gap:8px;justify-content:center;margin-top:26px}
.dots i{width:8px;height:8px;border-radius:50%;background:#bbb}
.dots i:first-child{background:var(--ink)}

/* memories */
.memories{position:absolute;top:1300px;left:140px;width:920px;display:flex;gap:40px}
.memories-photo{width:448px;height:372px;border-radius:12px;background:linear-gradient(160deg,#c9ced4,#8b939c 60%,#5f666e)}
.memories-copy{padding-top:44px;width:430px}
.memories-copy h2{font-size:40px;margin-bottom:20px}
.memories-copy p{font-size:12.5px;line-height:1.7;margin-bottom:14px}

/* destinations */
.destinations{position:absolute;top:1800px;left:0;width:1200px;height:440px;background:linear-gradient(180deg,var(--blue-dark),var(--blue))}
.destinations h2{color:var(--white);text-align:center;font-size:40px;margin-top:58px}
.dest-row{position:absolute;top:148px;left:120px;display:flex;gap:20px}
.dest{width:306px;height:384px;border-radius:14px;overflow:hidden;position:relative;box-shadow:0 10px 24px rgba(0,0,0,.18)}
.dest-photo{position:absolute;inset:0}
.dest-cap{position:absolute;left:0;right:0;bottom:0;height:110px;background:linear-gradient(0deg,rgba(0,0,0,.75),rgba(0,0,0,0));display:flex;flex-direction:column;align-items:center;justify-content:flex-end;padding-bottom:22px}
.dest-cap h3{color:var(--white);font-size:22px}
.dest-cap span{color:var(--white);font-size:11px;font-weight:600;margin-top:4px}
.view-more{position:absolute;top:2376px;left:0;width:1200px;text-align:center}

/* compare */
.compare{position:absolute;top:2510px;left:140px;width:920px}
.tours{width:100%;border-collapse:collapse;margin-top:30px;font-size:13px}
.tours th{background:var(--ink);color:var(--white);text-align:left;padding:16px 28px;font-size:12px;text-transform:uppercase;font-weight:600}
.tours th:first-child{border-radius:10px 0 0 10px}
.tours th:last-child{border-radius:0 10px 10px 0}
.tours td{padding:22px 28px;border-bottom:1px solid var(--line)}

/* gift */
.gift{position:absolute;top:2840px;left:140px;width:920px;display:flex;justify-content:space-between}
.gift-copy{width:440px;padding-top:50px}
.gift-copy h2{font-size:40px;margin-bottom:18px}
.gift-copy p{font-size:12.5px;line-height:1.7;margin-bottom:24px}
.gift-photo{width:440px;height:340px;border-radius:12px;background:linear-gradient(140deg,#6d8196,#9fb0bf 45%,#3d4650)}

/* expect */
.expect{position:absolute;top:3290px;left:0;width:1200px}
.steps{display:flex;justify-content:center;gap:76px;margin-top:34px}
.step{width:152px;height:112px;border:1px solid var(--line);border-radius:8px;background:var(--soft);display:flex;flex-direction:column;align-items:center;justify-content:center;gap:12px}
.step span{font-family:"Oswald",sans-serif;font-size:13px;text-transform:uppercase;color:var(--ink)}

/* faq */
.faq{position:absolute;top:3580px;left:248px;width:704px}
.faq-list{margin-top:32px;list-style:none}
.faq-list li{background:var(--soft);border:1px solid var(--line);border-radius:6px;height:44px;margin-bottom:10px;display:flex;align-items:center;justify-content:space-between;padding:0 22px;font-size:12px;font-weight:600;text-transform:uppercase;color:var(--ink)}

/* footer */
.footer{position:absolute;top:3980px;left:0;width:1200px;height:396px;background:var(--footer);color:#ddd}
.footer-brand{position:absolute;left:100px;top:120px;display:flex;align-items:center;gap:12px;color:var(--white);font-weight:700;font-size:32px}
.footer-brand .brand-dot{width:52px;height:52px}
.fcol{position:absolute;top:56px}
.fcol h3{color:var(--white);font-size:20px;margin-bottom:18px}
.fcol ul{list-style:none}
.fcol li{font-size:12px;line-height:2.1}
.contact li{display:flex;align-items:center;gap:8px}
.copyright{position:absolute;left:0;right:0;bottom:0;height:62px;border-top:1px solid #2c2c2c;display:flex;align-items:center;justify-content:center;font-size:12px;color:#aaa}
.to-top{position:absolute;right:32px;bottom:14px;width:40px;height:40px;border-radius:50%;background:var(--blue);display:flex;align-items:center;justify-content:center}
</style>
</head>
<body>

<header class="hero">
  <div class="hero-photo" role="img" aria-label="Two smiling passengers wearing headsets inside a helicopter above a city skyline"></div>
  <div class="hero-shade"></div>
  <nav class="nav">
    <a class="brand" href="#"><span class="brand-dot"></span>skyPARLOR</a>
    <ul class="menu">
      <li><a href="#">Home</a></li>
      <li><a href="#">Sarasota</a></li>
      <li><a href="#">Tampa</a></li>
      <li><a href="#">Special Events</a></li>
      <li><a href="#">Influencer</a></li>
      <li><a href="#">Contact Us</a></li>
      <li><a class="btn" href="#">Book Your SkyParlor</a></li>
    </ul>
  </nav>
  <div class="hero-copy">
    <h1>The Ultimate<br>Helicopter</h1>
    <p>Experience say yes to new adventures</p>
    <a class="btn" href="#">Book Your SkyParlor</a>
  </div>
</header>

<form class="booking">
  <div class="field"><label>From</label><span>Tokyo, Japan</span></div>
  <div class="field"><label>To</label><span>Berlin, Germany</span></div>
  <div class="field"><label>Departure</label><span>Jan 12, 2026</span></div>
  <div class="field"><label>Return</label><span>Feb 12, 2026</span></div>
  <div class="search"><svg width="18" height="18" viewBox="0 0 24 24" fill="none" stroke="#fff" stroke-width="2.5"><circle cx="10" cy="10" r="7"/><path d="M15 15l6 6"/></svg></div>
</form>

<section class="reviews">
  <h2 class="section-title">What Customers Are Saying</h2>
  <div class="rating-name">Orbin Ratings</div>
  <div class="review-row">
    <article class="review">
      <div class="review-head"><span class="avatar" style="background:#6d7b8a">M</span><div><b>Marla Quint</b><span class="stars">★★★★★</span></div></div>
      <p>Had an incredible experience with SkyParlor. From the moment we arrived the team was friendly, professional, and well organized.</p>
      <a href="#">Read More</a>
    </article>
    <article class="review">
      <div class="review-head"><span class="avatar" style="background:#a0714b">R</span><div><b>Rafe Dunmore</b><span class="stars">★★★★★</span></div></div>
      <p>This was our Christmas gift for my son and he loved every minute. Everything ran smoothly and the views were amazing.</p>
      <a href="#">Read More</a>
    </article>
    <article class="review">
      <div class="review-head"><span class="avatar" style="background:#2f8a5b">O</span><div><b>Owen Castell</b><span class="stars">★★★★★</span></div></div>
      <p>Such a great experience! Our pilot was knowledgeable and made the flight feel easy. Would absolutely book again soon.</p>
      <a href="#">Read More</a>
    </article>
  </div>
  <div class="dots"><i></i><i></i><i></i></div>
</section>

<section class="memories">
  <div class="memories-photo" role="img" aria-label="Woman in sunglasses standing in front of a helicopter on a landing pad"></div>
  <div class="memories-copy">
    <h2>We Create Memories</h2>
    <p>SkyParlor offers some of the most exciting Florida helicopter tours, empowering you to design your own custom aerial adventure with special helicopter tours in Tampa and Sarasota. Whether you prefer a peaceful air conditioned ride or the thrill of a doors-off flight, we deliver.</p>
    <p>We also bring Gender Reveals to a whole new level with dramatic sky-high reveal drops that turn your announcement into an unforgettable celebration shared with everyone below.</p>
    <a class="btn" href="#">Read More</a>
  </div>
</section>

<section class="destinations">
  <h2>Choose Your SkyParlor</h2>
  <div class="dest-row">
    <article class="dest">
      <div class="dest-photo" role="img" aria-label="Aerial view of St. Augustine waterfront and marina" style="background:linear-gradient(170deg,#8fb6d6,#4f7f9e 55%,#2e4c3a)"></div>
      <div class="dest-cap"><h3>St. Augustine Florida</h3><span>Coming Soon</span></div>
    </article>
    <article class="dest">
      <div class="dest-photo" role="img" aria-label="Tampa downtown skyline above the river" style="background:linear-gradient(170deg,#6fa0d0,#3a6f9e 55%,#23445f)"></div>
      <div class="dest-cap"><h3>Tampa Florida</h3><span>Book Now</span></div>
    </article>
    <article class="dest">
      <div class="dest-photo" role="img" aria-label="Sarasota palm-lined waterfront" style="background:linear-gradient(170deg,#9cc4e0,#5d8e6a 60%,#33503a)"></div>
      <div class="dest-cap"><h3>Sarasota Florida</h3><span>Book Now</span></div>
    </article>
  </div>
</section>
<div class="view-more"><a class="btn" href="#">View More</a></div>

<section class="compare">
  <h2 class="section-title">Compare Our Tours</h2>
  <table class="tours">
    <thead><tr><th>Tour</th><th>Duration</th><th>Route</th><th>Price</th></tr></thead>
    <tbody>
      <tr><td>City Lights</td><td>30 min</td><td>Downtown + Bay</td><td>$199</td></tr>
      <tr><td>Sunset Tour</td><td>45 min</td><td>City + Coastline</td><td>$259</td></tr>
    </tbody>
  </table>
</section>

<section class="gift">
  <div class="gift-copy">
    <h2>Gift Cards</h2>
    <p>Give the gift of an unforgettable adventure with SkyParlor gift cards. Perfect for birthdays, anniversaries, holidays or any special occasion, our gift cards allow recipients to choose their own scenic ride over Tampa or Sarasota. Easy to purchase online and instantly redeemable, they make every celebration a little more breathtaking.</p>
    <a class="btn" href="#">Read More</a>
  </div>
  <div class="gift-photo" role="img" aria-label="Passengers inside a helicopter cabin looking out over the coast"></div>
</section>

<section class="expect">
  <h2 class="section-title">What To Expect</h2>
  <div class="steps">
    <div class="step"><svg width="36" height="36" viewBox="0 0 24 24" fill="none" stroke="#1f5fa8" stroke-width="1.6"><path d="M12 21s-7-6.5-7-12a7 7 0 0 1 14 0c0 5.5-7 12-7 12z"/><circle cx="12" cy="9" r="2.5"/></svg><span>Arrive</span></div>
    <div class="step"><svg width="36" height="36" viewBox="0 0 24 24" fill="none" stroke="#1f5fa8" stroke-width="1.6"><path d="M12 3l8 3v6c0 5-3.5 8-8 9-4.5-1-8-4-8-9V6z"/><path d="M8.5 12l2.5 2.5 4.5-5"/></svg><span>Safety Briefing</span></div>
    <div class="step"><svg width="36" height="36" viewBox="0 0 24 24" fill="none" stroke="#1f5fa8" stroke-width="1.6"><rect x="4" y="4" width="16" height="17" rx="2"/><path d="M8 3v3M16 3v3M8 13l3 3 5-6"/></svg><span>Check In</span></div>
    <div class="step"><svg width="36" height="36" viewBox="0 0 24 24" fill="none" stroke="#1f5fa8" stroke-width="1.6"><rect x="3" y="7" width="18" height="13" rx="2"/><path d="M8 7l2-3h4l2 3"/><circle cx="12" cy="13.5" r="3.5"/></svg><span>Photos</span></div>
    <div class="step"><svg width="36" height="36" viewBox="0 0 24 24" fill="none" stroke="#1f5fa8" stroke-width="1.6"><path d="M3 5h14M10 5v4"/><path d="M5 9h9a4 4 0 0 1 4 4v2H7a2 2 0 0 1-2-2z"/><path d="M18 13h3M7 19h10"/></svg><span>Flight</span></div>
  </div>
</section>

<section class="faq">
  <h2 class="section-title">Frequently Asked Questions</h2>
  <ul class="faq-list">
    <li>What makes SkyParlor helicopter tours unique?<svg width="12" height="12" viewBox="0 0 12 12" fill="none" stroke="#141414" stroke-width="1.8"><path d="M2 8l4-4 4 4"/></svg></li>
    <li>How do I book a helicopter tour?<svg width="12" height="12" viewBox="0 0 12 12" fill="none" stroke="#141414" stroke-width="1.8"><path d="M2 4l4 4 4-4"/></svg></li>
    <li>Are SkyParlor flights safe?<svg width="12" height="12" viewBox="0 0 12 12" fill="none" stroke="#141414" stroke-width="1.8"><path d="M2 4l4 4 4-4"/></svg></li>
    <li>What should I expect during my helicopter tour?<svg width="12" height="12" viewBox="0 0 12 12" fill="none" stroke="#141414" stroke-width="1.8"><path d="M2 4l4 4 4-4"/></svg></li>
  </ul>
</section>

<footer class="footer">
  <div class="footer-brand"><span class="brand-dot"></span>skyPARLOR</div>
  <div class="fcol" style="left:420px">
    <h3>Company</h3>
    <ul><li>Home</li><li>Sarasota</li><li>Tampa</li><li>Special Events</li><li>Influencer</li><li>Contact Us</li><li>Book Your SkyParlor</li></ul>
  </div>
  <div class="fcol contact" style="left:620px">
    <h3>SkyParlor, LLC</h3>
    <ul>
      <li><svg width="12" height="12" viewBox="0 0 24 24" fill="#ddd"><path d="M6.6 10.8a15 15 0 0 0 6.6 6.6l2.2-2.2a1 1 0 0 1 1-.25 11.4 11.4 0 0 0 3.6.57 1 1 0 0 1 1 1V20a1 1 0 0 1-1 1A17 17 0 0 1 3 4a1 1 0 0 1 1-1h3.5a1 1 0 0 1 1 1c0 1.25.2 2.45.57 3.6a1 1 0 0 1-.25 1z"/></svg>(844) 555-0147 (Tampa) | (941) 555-0182</li>
      <li><svg width="12" height="12" viewBox="0 0 24 24" fill="none" stroke="#ddd" stroke-width="2"><rect x="3" y="5" width="18" height="14" rx="2"/><path d="M3 7l9 6 9-6"/></svg>info@skyparlor-example.com</li>
    </ul>
  </div>
  <div class="fcol" style="left:948px">
    <h3>Hotline Hours</h3>
    <ul><li>Mon 09:00 am – 05:30 pm</li><li>Tue 09:00 am – 05:30 pm</li><li>Wed 09:00 am – 05:30 pm</li><li>Thu 09:00 am – 05:30 pm</li><li>Fri 09:00 am – 05:30 pm</li><li>Sat 09:00 am – 05:30 pm</li><li>Sun 09:00 am – 05:30 pm</li></ul>
  </div>
  <div class="copyright">Copyright © 2026 SkyParlor. All Rights Reserved</div>
  <a class="to-top" href="#"><svg width="14" height="14" viewBox="0 0 12 12" fill="none" stroke="#fff" stroke-width="2"><path d="M2 8l4-4 4 4"/></svg></a>
</footer>

</body>
</html>
```